German Headhunter/ HR Consultancy needs Business Cards Design

We need a business Card Design for our Company in Stuttgart. We are specialized as Headhunter/ HR Consultancy in Placement of specialist and managers in permanent employment. Please refer to our business logo.

```html
<!DOCTYPE html>
<html lang="de">
<head>
<meta charset="utf-8">
<title>Kernwerk Personalberatung – Visitenkarten</title>
<link rel="stylesheet" href="https://fonts.googleapis.com/css2?family=Montserrat:wght@500;700&family=Arimo:wght@400;700&display=swap">
<style>
  :root {
    --brand-blue: #3b56a8;
    --card-grey: #96979b;
    --paper: #ffffff;
    --stage: #2b2b2d;
    --ink-light: #ffffff;
  }
  * { box-sizing: border-box; margin: 0; padding: 0; }
  html, body {
    width: 1200px; height: 1015px; overflow: hidden;
    background: var(--stage);
  }
  .canvas { position: relative; width: 1200px; height: 1015px; }

  .card {
    position: absolute;
    width: 600px; height: 343px;
    overflow: hidden;
    box-shadow: 0 10px 28px rgba(0,0,0,.45);
  }

  /* Front: grey with wordmark */
  .card--front {
    left: 110px; top: 110px;
    background: var(--card-grey);
    display: flex; align-items: center; justify-content: center;
  }
  .wordmark {
    display: flex; align-items: center; gap: 16px;
    color: var(--brand-blue);
    font-family: "Montserrat", sans-serif; font-weight: 700;
  }
  .wordmark__square {
    width: 46px; height: 46px; background: var(--brand-blue);
  }
  .wordmark__name { font-size: 40px; line-height: 1; letter-spacing: 1px; }
  .wordmark__sub { font-size: 15px; letter-spacing: 2.5px; margin-top: 6px; }

  /* Back: white with blue band */
  .card--back {
    left: 490px; top: 560px;
    background: var(--paper);
  }
  .card__band { position: absolute; inset: 0; width: 100%; height: 100%; }

  .contact {
    position: absolute; left: 40px; top: 118px;
    color: var(--ink-light);
    font-family: "Arimo", sans-serif;
  }
  .contact__name {
    font-family: "Montserrat", sans-serif; font-weight: 700;
    font-size: 21px; letter-spacing: .5px;
  }
  .contact__role { font-size: 12.5px; letter-spacing: 1px; margin-bottom: 12px; }
  .contact__list { list-style: none; font-size: 14px; line-height: 1.45; }
  .contact__list li { display: flex; align-items: center; gap: 8px; }
  .contact__list svg { width: 13px; height: 13px; flex: none; }
  .contact__address { font-size: 14px; line-height: 1.35; margin-top: 12px; }

  .back-mark {
    position: absolute; right: 34px; top: 30px;
    display: flex; align-items: center; gap: 10px;
    color: var(--brand-blue);
    font-family: "Montserrat", sans-serif; font-weight: 700;
    font-size: 26px; letter-spacing: 1px;
  }
  .back-mark__square { width: 30px; height: 30px; background: var(--brand-blue); }
</style>
</head>
<body>
<main class="canvas">

  <section class="card card--front" aria-label="Vorderseite">
    <div class="wordmark">
      <span class="wordmark__square"></span>
      <div>
        <div class="wordmark__name">KERNWERK</div>
        <div class="wordmark__sub">PERSONALBERATUNG</div>
      </div>
    </div>
  </section>

  <section class="card card--back" aria-label="Rückseite">
    <svg class="card__band" viewBox="0 0 600 343" preserveAspectRatio="none" aria-hidden="true">
      <polygon points="0,100 395,100 460,300 0,300" fill="var(--brand-blue)"/>
    </svg>

    <div class="back-mark">
      <span class="back-mark__square"></span>
      <span>KERNWERK</span>
    </div>

    <div class="contact">
      <div class="contact__name">JONATHAN SMITH</div>
      <div class="contact__role">MANAGING DIRECTOR</div>
      <ul class="contact__list">
        <li>
          <svg viewBox="0 0 24 24" fill="none" stroke="currentColor" stroke-width="2.4"><path d="M5 3h4l2 5-3 2a11 11 0 0 0 6 6l2-3 5 2v4a2 2 0 0 1-2 2A18 18 0 0 1 3 5a2 2 0 0 1 2-2z"/></svg>
          044-123 456 789
        </li>
        <li>
          <svg viewBox="0 0 24 24" fill="none" stroke="currentColor" stroke-width="2.4"><rect x="2" y="5" width="20" height="14"/><path d="M2 5l10 8 10-8"/></svg>
          info@webname.com
        </li>
        <li>
          <svg viewBox="0 0 24 24" fill="none" stroke="currentColor" stroke-width="2.2"><circle cx="12" cy="12" r="10"/><path d="M2 12h20M12 2c3 3 3 17 0 20M12 2c-3 3-3 17 0 20"/></svg>
          www.websitename.com
        </li>
      </ul>
      <p class="contact__address">421, Address line goes here<br>45452,Country Name</p>
    </div>
  </section>

</main>
</body>
</html>
```